Business Cards for a law firm

Business cards for our law firm. Use our silhoette logo and OAK PARTNERS - check our website (www.oakpartners.example)

Contact Information for Business Card

our silhouette logo, OAK PARTNERS, 800-555-0147, Dorian Pemberton, dorian@oakpartners.example

Requirements
Must have
• our silhouette logo, OAK PARTNERS, 800-555-0147, Dorian Pemberton, dorian@oakpartners.example

```html
<!DOCTYPE html>
<html lang="en">
<head>
<meta charset="utf-8">
<title>Oak Partners – Business Cards</title>
<link rel="stylesheet" href="https://fonts.googleapis.com/css2?family=Jost:wght@400&family=Roboto:wght@300;400;700&display=swap">
<style>
  :root {
    --backdrop: #e2e7e9;
    --navy: #22336b;
    --navy-deep: #1d2b5c;
    --sky: #3e9bd7;
    --white: #ffffff;
    --mark-faint: rgba(255, 255, 255, 0.1);
  }
  * { margin: 0; padding: 0; box-sizing: border-box; }
  html, body {
    width: 1200px;
    height: 960px;
    overflow: hidden;
    background: var(--backdrop);
  }
  .canvas {
    position: relative;
    width: 1200px;
    height: 960px;
  }
  .card {
    position: absolute;
    left: 248px;
    width: 704px;
    height: 402px;
    background: var(--navy);
    overflow: hidden;
  }
  .card--front { top: 58px; }
  .card--back { top: 500px; }

  .front-pattern {
    position: absolute;
    inset: 0;
    background:
      linear-gradient(35deg, var(--navy-deep) 0%, var(--navy) 45%, #2f6fb4 72%, var(--sky) 100%);
  }
  .brand-mark {
    position: absolute;
    left: 163px;
    top: 162px;
    width: 80px;
    height: 80px;
    background: var(--white);
  }
  .brand-name {
    position: absolute;
    left: 260px;
    top: 154px;
    color: var(--white);
    font-family: "Jost", sans-serif;
    font-weight: 400;
    font-size: 46px;
    line-height: 40px;
    letter-spacing: 5px;
    white-space: nowrap;
  }

  .back-mark {
    position: absolute;
    left: 308px;
    top: 156px;
    width: 88px;
    height: 88px;
    background: var(--mark-faint);
  }
  .holder-name {
    position: absolute;
    left: 26px;
    top: 186px;
    color: var(--white);
    font-family: "Roboto", sans-serif;
    font-size: 28px;
    letter-spacing: 0.5px;
    white-space: nowrap;
  }
  .holder-name .first { font-weight: 700; }
  .holder-name .last { font-weight: 300; }

  .contact-list {
    position: absolute;
    left: 411px;
    top: 171px;
    list-style: none;
    font-family: "Roboto", sans-serif;
    font-weight: 400;
    font-size: 18px;
    color: var(--white);
    letter-spacing: 0.5px;
    white-space: nowrap;
  }
  .contact-list li {
    display: flex;
    align-items: center;
    height: 28px;
  }
  .contact-icon {
    width: 17px;
    height: 17px;
    margin-right: 10px;
    flex: none;
  }
  .website {
    position: absolute;
    left: 0;
    right: 0;
    top: 334px;
    text-align: center;
    font-family: "Roboto", sans-serif;
    font-weight: 400;
    font-size: 18px;
    letter-spacing: 0.5px;
    color: var(--white);
  }
</style>
</head>
<body>
<main class="canvas">
  <section class="card card--front">
    <div class="front-pattern" role="img" aria-label="Repeating pattern of the firm's mark fading from navy to light blue"></div>
    <div class="brand-mark" role="img" aria-label="Place for the firm's silhouette mark"></div>
    <div class="brand-name">OAK<br>PARTNERS</div>
  </section>

  <section class="card card--back">
    <div class="back-mark" role="img" aria-label="Faint place for the firm's silhouette mark"></div>
    <p class="holder-name"><span class="first">DORIAN</span> <span class="last">PEMBERTON</span></p>
    <ul class="contact-list">
      <li>
        <svg class="contact-icon" viewBox="0 0 24 24" aria-hidden="true">
          <path fill="#fff" d="M6.6 10.8c1.4 2.8 3.8 5.1 6.6 6.6l2.2-2.2c.3-.3.7-.4 1-.2 1.1.4 2.3.6 3.6.6.6 0 1 .4 1 1V20c0 .6-.4 1-1 1C10.6 21 3 13.4 3 4c0-.6.4-1 1-1h3.5c.6 0 1 .4 1 1 0 1.3.2 2.5.6 3.6.1.3 0 .7-.2 1l-2.3 2.2z"/>
        </svg>
        800-555-0147
      </li>
      <li>
        <svg class="contact-icon" viewBox="0 0 24 24" aria-hidden="true">
          <rect x="2" y="5" width="20" height="14" rx="1.5" fill="none" stroke="#fff" stroke-width="2"/>
          <path d="M3 6l9 7 9-7" fill="none" stroke="#fff" stroke-width="2"/>
        </svg>
        dorian@oakpartners.example
      </li>
    </ul>
    <p class="website">www.oakpartners.example</p>
  </section>
</main>
</body>
</html>
```